Printed Circuit Board Company Web Site Design - Please see new file 82012 web design

We are a printed circuit board manufacturer. Need a company professional web site to allow our potential customers to know more about our background, capability and our products. The web site will contain three languages, which are Chinese, English and Japanese. Our audience are mainly electronic companies that procure printed circuit boards. I have a word document that have all the required text in all three languages. The final design should communicate the impression that we embrace quality, trustworthiness and long term partnership business principles.
We should have sections that allow us to post pictures of our facilities.
I have added the three files in three different languages.
Some of the information is below:
Background
RDV Harbourline Limited (RDV) was set up in Hong Kong in 2007 by two Hong Kong entrepreneurs, Mr. Tak Wong and Mr. Lok Fai. We acquired the single sided printed circuit board factory located in Dongguan City, Guangdong Province, China, from Tovand Corporation of the U.S. in 2007. In addition to RDV, Mr. Wong and Mr. Fai also own Halberd Technology Company Limited, a semiconductor company based in Hong Kong since 1997 with a total investment of over US$100 million. Halberd is engaged in the manufacturing of flexible substrates and MEMS assembly business.
RDV has been awarded TS 16949 and ISO14000 certificates since 2009 and 2004 respectively.
Business Principles
RDV Harbourline Limited strives to be a professional top notched printed circuit board supplier. We embrace four “EXCELLENCE” principles, namely, excellence in quality, excellence in prices, excellence in services and excellence in on time delivery.
We approach each customer with a long-term partnership view that delivers the lowest ownership costs and highest total values to our customers. We customize quotations and solutions in order to allow our customers to win more businesses. We believe by thinking from our customers’ points of view we will be able to create a WIN-WIN relationship.
Customers
Due to our excellent quality, services and production systems, RDV Harbourline Limited manage to service a number of large Japanese and US customers, which include:
Technical capability overview
Below is an overview of our current capability:
Target Market(s)
Electronic companies buyers
Industry/Entity Type
Business
Requirements
Must have
- Capability description
Should not have
- no cartoon

```html
<!DOCTYPE html>
<html lang="en">
<head>
<meta charset="utf-8">
<title>RDV Harbourline Limited – Home</title>
<link rel="stylesheet" href="https://fonts.googleapis.com/css2?family=Arimo:wght@400;700&family=Cinzel:wght@400;600&family=Alegreya:ital@0;1&display=swap">
<style>
  :root{
    --green:#0d7a62;
    --green-dark:#0a6552;
    --green-deep:#075645;
    --page-bg:#eceeed;
    --white:#ffffff;
    --nav-top:#4a4a4a;
    --nav-bottom:#141414;
    --tab-gold:#f4c77b;
    --text:#4a4a4a;
    --rule:#c9c9c9;
    --head-green:#127a63;
  }
  *{margin:0;padding:0;box-sizing:border-box}
  html,body{width:1200px;height:833px;overflow:hidden}
  body{position:relative;background:var(--page-bg);font-family:"Arimo",Arial,sans-serif;color:var(--text)}

  .site-header{position:absolute;left:0;top:0;width:1200px;height:80px;background:var(--green-dark)}
  .site-header__centre{position:absolute;left:241px;top:0;width:716px;height:80px;background:linear-gradient(180deg,#0f846a,#0b6f59)}
  .brand{position:absolute;left:22px;top:16px;color:var(--white);font-family:"Arimo",Arial,sans-serif;font-weight:700;line-height:1}
  .brand__name{font-size:28px;letter-spacing:4px;display:block}
  .brand__sub{font-size:10px;letter-spacing:1px;display:block;margin-top:3px}
  .header-phone{position:absolute;left:581px;top:44px;display:flex;align-items:center;gap:5px;color:var(--white);font-size:13px;font-weight:700}

  .main-nav{position:absolute;left:0;top:80px;width:1200px;height:27px;background:linear-gradient(180deg,var(--nav-top),var(--nav-bottom));border-top:1px solid #777}
  .main-nav__item{position:absolute;top:0;height:27px;line-height:26px;font-family:"Cinzel",serif;font-weight:600;font-size:10.5px;letter-spacing:.3px;color:var(--white);text-decoration:none;white-space:nowrap}
  .main-nav__item--active{background:var(--tab-gold);color:#3a2a10;padding:0 7px;left:288px;width:46px}
  .login-tab{position:absolute;left:876px;top:0;width:58px;height:27px;background:var(--tab-gold);display:flex;align-items:center;justify-content:center;gap:4px;font-size:10px;font-weight:700;color:#2a2a2a}

  .content{position:absolute;left:241px;top:107px;width:716px;height:607px;background:var(--white);box-shadow:0 0 8px rgba(0,0,0,.12)}

  .principles{position:absolute;left:45px;top:38px}
  .principles__lead{font-family:"Alegreya",serif;font-style:italic;font-size:32px;color:var(--head-green);line-height:34px}
  .principles__title{font-family:"Alegreya",serif;font-size:34px;color:var(--head-green);line-height:34px;margin-left:-4px;transform:scaleX(.85);transform-origin:left}
  .principles__sub{font-family:"Cinzel",serif;font-size:22px;letter-spacing:5.5px;color:var(--head-green);line-height:26px}
  .principles__list{position:absolute;left:25px;top:146px;width:226px;list-style:none}
  .principles__list li{height:32px;border-bottom:1px solid var(--rule);display:flex;align-items:center;gap:8px;padding-left:6px;font-family:"Alegreya",serif;font-size:19px;color:var(--head-green);white-space:nowrap;overflow:visible}
  .principles__text{display:inline-block;transform:scaleX(.88);transform-origin:left center}

  .hero-visual{position:absolute;left:255px;top:8px;width:455px;height:325px;background:radial-gradient(ellipse at 60% 50%,#dde4ec 0%,#f2f4f7 55%,#ffffff 85%)}

  .welcome{position:absolute;left:31px;top:345px;width:357px}
  .section-title{font-size:13.5px;font-weight:700;color:var(--head-green);letter-spacing:.1px;white-space:nowrap}
  .welcome p{margin-top:11px;font-size:9.2px;line-height:14.8px;text-align:justify}
  .welcome a{color:#333;font-weight:700;text-decoration:underline}

  .facility-frame{position:absolute;left:407px;top:341px;width:279px;height:172px;border:1px solid #d0d0d0;padding:10px 7px}
  .facility-photo{width:263px;height:151px;background:linear-gradient(135deg,#9aa7a8,#cfd5d3 55%,#b86a4a)}

  .customers{position:absolute;left:31px;top:525px;width:660px}
  .carousel{position:absolute;left:4px;top:25px;width:656px;height:50px;display:flex;align-items:center}
  .carousel__arrow{flex:none}
  .carousel__track{flex:1;display:flex;justify-content:space-around;align-items:center;padding:0 8px}
  .customer-name{font-size:17px;font-weight:700;color:#555;white-space:nowrap}

  .site-footer{position:absolute;left:0;top:714px;width:1200px;height:96px;background:var(--green)}
  .footer-links{position:absolute;left:272px;top:8px;color:var(--white)}
  .footer-links h3{font-size:8px;font-weight:700;letter-spacing:.3px}
  .footer-links__cols{display:flex;margin-top:11px}
  .footer-links ul{list-style:none;width:111px}
  .footer-links li{font-size:7.5px;line-height:12px}
  .footer-links li::before{content:"▸";font-size:6px;color:#f4c77b;margin-right:4px}
  .footer-address{position:absolute;right:272px;top:10px;text-align:right;color:var(--white);font-size:7.5px;line-height:12px;font-style:normal}
  .footer-address strong{font-size:8px}
  .copyright{position:absolute;left:0;top:810px;width:1200px;height:23px;background:var(--green-deep);color:var(--white);font-size:7.5px;font-weight:700;text-align:center;line-height:24px}
</style>
</head>
<body>
  <header class="site-header">
    <div class="site-header__centre">
      <div class="brand">
        <span class="brand__name">RDV</span>
        <span class="brand__sub">Harbourline Limited</span>
      </div>
      <div class="header-phone">
        <svg width="18" height="14" viewBox="0 0 18 14" aria-hidden="true"><path d="M2 9c3-6 9-8 14-7-3 1-5 3-6 5l3 2c-3 3-8 4-11 3z" fill="#fff"/></svg>
        <span>(852) 2460 5183</span>
      </div>
    </div>
  </header>

  <nav class="main-nav">
    <a class="main-nav__item main-nav__item--active" href="#">HOME</a>
    <a class="main-nav__item" style="left:373px" href="#">PRODUCTS</a>
    <a class="main-nav__item" style="left:475px" href="#">SERVICES</a>
    <a class="main-nav__item" style="left:568px" href="#">TECHNICAL CAPABILITIES</a>
    <a class="main-nav__item" style="left:747px" href="#">CONTACT US</a>
    <div class="login-tab">
      <svg width="11" height="13" viewBox="0 0 11 13" aria-hidden="true"><path d="M3 6V4a2.5 2.5 0 0 1 5 0v2" fill="none" stroke="#555" stroke-width="1.4"/><rect x="1" y="6" width="9" height="7" rx="1" fill="#777"/></svg>
      <span>login</span>
    </div>
  </nav>

  <main class="content">
    <section class="principles">
      <div class="principles__lead">We embrace four</div>
      <div class="principles__title">“EXCELLENCE”</div>
      <div class="principles__sub">PRINCIPLES</div>
    </section>
    <ul class="principles__list">
      <li><svg width="16" height="14" viewBox="0 0 16 14" aria-hidden="true"><path d="M1 8l4 4L15 1" fill="none" stroke="#127a63" stroke-width="2"/></svg><span class="principles__text">Excellence in quality</span></li>
      <li><svg width="16" height="14" viewBox="0 0 16 14" aria-hidden="true"><path d="M1 8l4 4L15 1" fill="none" stroke="#127a63" stroke-width="2"/></svg><span class="principles__text">Excellence in prices</span></li>
      <li><svg width="16" height="14" viewBox="0 0 16 14" aria-hidden="true"><path d="M1 8l4 4L15 1" fill="none" stroke="#127a63" stroke-width="2"/></svg><span class="principles__text">Excellence in services</span></li>
      <li><svg width="16" height="14" viewBox="0 0 16 14" aria-hidden="true"><path d="M1 8l4 4L15 1" fill="none" stroke="#127a63" stroke-width="2"/></svg><span class="principles__text">Excellence in on time delivery</span></li>
    </ul>
    <div class="hero-visual" role="img" aria-label="Illustration of floating glass screens with a world map, bar chart and a monitor"></div>

    <section class="welcome">
      <h2 class="section-title">WELCOME TO RDV HARBOURLINE LIMITED (RDV)</h2>
      <p>RDV Harbourline Limited (RDV) was set up in Hong Kong in 2007 by two Hong Kong entrepreneurs, &nbsp;Mr. Tak Wong and Mr. Lok Fai. &nbsp;We acquired the single sided printed circuit board factory located in Dongguan City, Guangdong Province, China, from Tovand Corporation of the U.S. in 2007. In addition to RDV, Mr. Wong and Mr. Fai also own Halberd Technology Company Limited, &nbsp;a semiconductor company based in Hong Kong since 1997 with a total investment of over US$100 million. &nbsp;Halberd is engaged in the manufacturing of flexible substrates and the assembly of <a href="#">Micro Electro Mechanical Systems (MEMS).</a></p>
    </section>

    <div class="facility-frame">
      <div class="facility-photo" role="img" aria-label="Photograph of technicians working at machines on the factory floor"></div>
    </div>

    <section class="customers">
      <h2 class="section-title">CUSTOMERS</h2>
      <div class="carousel">
        <svg class="carousel__arrow" width="14" height="16" viewBox="0 0 14 16" aria-hidden="true"><path d="M11 2L4 8l7 6" fill="none" stroke="#333" stroke-width="3"/></svg>
        <div class="carousel__track">
          <span class="customer-name">Korvane</span>
          <span class="customer-name">Tessaro</span>
          <span class="customer-name">Lumeric</span>
          <span class="customer-name">Oberly</span>
          <span class="customer-name">Marwick International</span>
        </div>
        <svg class="carousel__arrow" width="14" height="16" viewBox="0 0 14 16" aria-hidden="true"><path d="M3 2l7 6-7 6" fill="none" stroke="#333" stroke-width="3"/></svg>
      </div>
    </section>
  </main>

  <footer class="site-footer">
    <div class="footer-links">
      <h3>POPULAR LINKS</h3>
      <div class="footer-links__cols">
        <ul>
          <li>Sitemap</li><li>Circuit Boardas</li><li>Capabilities</li><li>Industries Served</li><li>About Us</li>
        </ul>
        <ul>
          <li>Contact Us</li><li>Resources</li><li>Service Center</li><li>News &amp; Events</li><li>Privacy Policy</li>
        </ul>
      </div>
    </div>
    <address class="footer-address">
      <strong>RDV Harbourline Limited</strong><br>
      18/F Kestrel Plaza<br>
      27 Marlow Road<br>
      Tin Hau, HONG KONG<br>
      Telephone: (852)24605183<br>
      Fax: (852)24605190<br>
      Email: Sales@rdvboard.example
    </address>
  </footer>
  <div class="copyright">COPYRIGHT © 2012 RDV HARBOURLINE LIMITED. ALL RIGHTS RESERVED</div>
</body>
</html>
```